VeraMosk Powerpoint design

We've recently redesigned our logos and would like a single presentation format that we can easily interchange the logos attached into. The presentation will be used for general company sales information. The group is called VeraMosk and has 2 companies, k7datagrove and Copper Thread. We're an IT services company who specialises in Broadband and general network services.

Target Market(s)

Professional

```html
<!DOCTYPE html>
<html lang="en">
<head>
<meta charset="utf-8">
<title>VeraMosk presentation template</title>
<link rel="stylesheet" href="https://fonts.googleapis.com/css2?family=Poppins:wght@300;600;700&family=Mulish:wght@400;600&display=swap">
<style>
:root{
  --page:#dfe0e2;
  --ink:#1e1e1e;
  --muted:#3a3a3a;
  --blue:#29a8e0;
  --tag:#2b2b2b;
  --green:#0f6b35;
  --light:#f0f0f0;
  --white:#ffffff;
  --rule:#d6d6d6;
}
*{box-sizing:border-box;margin:0;padding:0}
html,body{width:1200px;height:3914px;overflow:hidden;background:var(--page)}
body{position:relative;font-family:"Mulish",sans-serif;color:var(--ink)}
.slide{position:absolute;left:99px;width:1001px;height:562px;overflow:hidden;background:var(--white)}
.s1{top:76px;background:#000}
.s2{top:705px;background:var(--light)}
.s3{top:1335px}
.s4{top:1966px}
.s5{top:2595px}
.s6{top:3225px;background:#07122a}
.abs{position:absolute}
.brand{position:absolute;font-family:"Mulish",sans-serif;font-weight:600;display:flex;align-items:center;gap:8px;white-space:nowrap}
.brand .dot{width:.7em;height:.7em;border-radius:50%;background:currentColor;opacity:.9}
.brand-main{font-size:34px;color:var(--ink)}
.tag{position:absolute;background:var(--tag);color:var(--white);font-family:"Poppins",sans-serif;font-weight:600;font-size:21px;display:flex;align-items:center;justify-content:center}
.footer-rule{position:absolute;left:0;right:0;height:1px;background:var(--rule)}
.footer-brand{font-size:22px;color:var(--ink)}
.photo{position:absolute}
/* slide 1 */
.s1 .photo{left:0;top:0;width:1001px;height:562px;background:radial-gradient(ellipse at 25% 55%,#1d3f86 0%,#0d2354 30%,#020814 60%,#000 75%)}
.s1 .brand-main{color:var(--white);font-size:46px;right:61px;top:36px}
.welcome{position:absolute;right:61px;top:190px;text-align:right;font-family:"Poppins",sans-serif;font-weight:700;font-size:46px;line-height:56px;color:var(--white)}
.welcome span{color:var(--blue)}
.s1 .sub{position:absolute;top:382px;font-size:26px;color:#6d6d6d}
/* slide 2 */
.card{position:absolute;top:138px;width:415px;height:380px;background:var(--white);box-shadow:3px 3px 6px rgba(0,0,0,.18);padding:52px 56px}
.card .brand{position:static;font-size:36px;color:var(--ink);margin-bottom:34px}
.card h3{font-family:"Poppins",sans-serif;font-weight:600;font-size:19px;line-height:23px;margin-bottom:22px}
.card p{font-size:12.5px;line-height:15px;color:var(--muted)}
/* slide 3 */
.about h2{position:absolute;left:47px;top:145px;width:370px;font-family:"Poppins",sans-serif;font-weight:600;font-size:22px;line-height:32px}
.about p{position:absolute;left:47px;top:225px;width:400px;font-size:12.8px;line-height:18.8px;color:var(--muted)}
.s3 .photo{left:523px;top:20px;width:448px;height:456px;border-radius:50%;background:radial-gradient(circle at 50% 50%,#4a7c8a 0%,#1f4350 45%,#0e1f28 80%,#fff 81%)}
/* slide 4 */
.service{position:absolute;left:32px;width:586px;height:120px;background:var(--blue);color:var(--white)}
.service svg{position:absolute;left:22px;top:28px}
.service h4{position:absolute;left:104px;top:16px;font-family:"Poppins",sans-serif;font-weight:600;font-size:16px}
.service p{position:absolute;left:104px;top:44px;width:460px;font-size:11.5px;line-height:12.6px}
/* slide 5 */
.s5 .photo{left:352px;top:0;width:649px;height:510px;background:linear-gradient(135deg,#0b2a4a 0%,#14617a 35%,#6a2a3a 60%,#0d4a55 85%,#0b2233 100%)}
.sol-box{position:absolute;left:33px;top:90px;width:392px;height:384px;background:var(--light);padding:36px 34px}
.sol-box h3{font-family:"Poppins",sans-serif;font-weight:600;font-size:19px;line-height:23px;margin-bottom:22px}
.sol-box p{font-size:12.2px;line-height:15px;color:var(--muted);margin-bottom:20px}
.sol-box ul{list-style:none}
.sol-box li{font-size:12px;line-height:25px;color:var(--muted);padding-left:16px;position:relative}
.sol-box li::before{content:"";position:absolute;left:2px;top:9px;border-left:5px solid var(--muted);border-top:4px solid transparent;border-bottom:4px solid transparent}
.overlay{position:absolute;left:559px;top:195px;width:300px;font-family:"Poppins",sans-serif;font-weight:600;font-size:24px;line-height:30px;color:var(--white)}
/* slide 6 */
.s6 .photo{left:0;top:0;width:1001px;height:562px;background:radial-gradient(ellipse at 40% 40%,#11305a 0%,#0a1c3a 45%,#050c1c 100%)}
.s6 .brand-main{left:0;right:0;justify-content:center;top:90px;color:var(--white);font-size:52px}
.thanks{position:absolute;left:0;right:0;top:270px;text-align:center;font-family:"Poppins",sans-serif;font-weight:300;font-size:56px;color:var(--white)}
</style>
</head>
<body>

<section class="slide s1">
  <div class="photo" role="img" aria-label="Glowing blue fibre optic strands sweeping across a black background"></div>
  <div class="brand brand-main">VeraMosk</div>
  <h1 class="welcome">Welcome to<br><span>VeraMosk group</span></h1>
  <div class="brand sub" style="right:270px">Copper Thread</div>
  <div class="brand sub" style="right:61px">k7datagrove</div>
</section>

<section class="slide s2">
  <div class="brand brand-main" style="left:56px;top:48px;">VeraMosk</div>
  <article class="card" style="left:56px">
    <div class="brand">Copper Thread</div>
    <h3>Lorem ipsum dolor sit amet, consectet</h3>
    <p>Sed ut perspiciatis unde omnis iste natus error sit voluptatem accusantium doloremque laudantium, totam rem aperiam, eaque ipsa quae ab illo inventore veritatis et quasi architecto beatae vitae dicta sunt explicabo. Nemo enim ipsam voluptatem quia voluptas sit aspernatur aut odit aut fugit, sed quia consequuntur magni dolores eos qui ratione voluptatem sequi nesciunt. Neque porro quisquam est, qui dolore</p>
  </article>
  <article class="card" style="left:504px">
    <div class="brand">k7datagrove</div>
    <h3>Lorem ipsum dolor sit amet, consectet</h3>
    <p>Sed ut perspiciatis unde omnis iste natus error sit voluptatem accusantium doloremque laudantium, totam rem aperiam, eaque ipsa quae ab illo inventore veritatis et quasi architecto beatae vitae dicta sunt explicabo. Nemo enim ipsam voluptatem quia voluptas sit aspernatur aut odit aut fugit, sed quia consequuntur magni dolores eos qui ratione voluptatem sequi nesciunt. Neque porro quisquam est, qui dolore</p>
  </article>
</section>

<section class="slide s3 about">
  <div class="brand brand-main" style="left:38px;top:24px;">VeraMosk</div>
  <div class="tag" style="left:216px;top:26px;width:132px;height:40px">About Us</div>
  <h2>Lorem Ipsum is simply dum text of the printing and</h2>
  <p>Sed ut perspiciatis unde omnis iste natus error sit voluptatem accusantium doloremque laudantium, totam rem aperiam, eaque ipsa quae ab illo inventore veritatis et quasi architecto beatae vitae dicta sunt explicabo. Nemo enim ipsam voluptatem quia voluptas sit aspernatur aut odit aut fugit, sed quia consequuntur magni dolores eos qui ratione voluptatem sequi nesciunt. Neque porro quisquam est, qui dolorem ipsum quia dolor sit amet, consectetur, adipisci velit, sed quia non numquam eius modi tempora incidunt ut labore et dolore magnam aliquam quaerat voluptatem. Ut enim ad minima veniam, quis nostrum exercitationem ullam corporis suscipit laboriosam, nisi ut aliquid ex ea commodi consequatur.</p>
  <div class="photo" role="img" aria-label="Two engineers working among server racks in a data centre"></div>
  <div class="footer-rule" style="top:507px"></div>
  <div class="brand footer-brand" style="left:18px;top:522px">Copper Thread</div>
  <div class="brand footer-brand" style="right:10px;top:522px">k7datagrove</div>
</section>

<section class="slide s4">
  <div class="brand brand-main" style="left:22px;top:14px;">VeraMosk</div>
  <div class="tag" style="left:196px;top:17px;width:131px;height:38px">Services</div>
  <svg class="abs" style="left:0;top:0" width="1001" height="360" viewBox="0 0 1001 360">
    <polygon points="577,0 1001,0 1001,350" fill="var(--green)"/>
    <polygon points="600,0 1001,0 1001,328" fill="#8fb4cf" role="img" aria-label="Close-up of network cables plugged into a switch"/>
  </svg>
  <div class="service" style="top:96px">
    <svg width="56" height="60" viewBox="0 0 56 60" fill="none" stroke="#fff" stroke-width="4" stroke-linecap="round"><path d="M6 22a32 32 0 0 1 44 0"/><path d="M14 31a21 21 0 0 1 28 0"/><path d="M21 40a10 10 0 0 1 14 0"/><circle cx="28" cy="48" r="3" fill="#fff"/></svg>
    <h4>Lorem ipsum dolor sit amet, consectetur</h4>
    <p>Sed ut perspiciatis unde omnis iste natus error sit voluptatem accusantium doloremque laudantium, totam rem aperiam, eaque ipsa quae ab illo inventore veritatis et quasi architecto beatae vitae dicta sunt explicabo. Nemo enim ipsam voluptatem quia voluptas sit aspernatur.</p>
  </div>
  <div class="service" style="top:231px">
    <svg width="56" height="60" viewBox="0 0 56 60" fill="none" stroke="#fff" stroke-width="4" stroke-linecap="round"><rect x="8" y="26" width="40" height="20" rx="3"/><path d="M16 26V12M40 26V12M18 36h4M26 36h4M34 36h4"/></svg>
    <h4>Lorem ipsum dolor sit amet, consectetur</h4>
    <p>Sed ut perspiciatis unde omnis iste natus error sit voluptatem accusantium doloremque laudantium, totam rem aperiam, eaque ipsa quae ab illo inventore veritatis et quasi architecto beatae vitae dicta sunt explicabo. Nemo enim ipsam voluptatem quia voluptas sit aspernatur.</p>
  </div>
  <div class="service" style="top:367px">
    <svg width="56" height="64" viewBox="0 0 56 64" fill="none" stroke="#fff" stroke-width="4" stroke-linecap="round"><rect x="16" y="24" width="24" height="36" rx="3"/><path d="M28 24V6M20 24V12M36 24V12M28 40v8"/></svg>
    <h4>Lorem ipsum dolor sit amet, consectetur</h4>
    <p>Sed ut perspiciatis unde omnis iste natus error sit voluptatem accusantium doloremque laudantium, totam rem aperiam, eaque ipsa quae ab illo inventore veritatis et quasi architecto beatae vitae dicta sunt explicabo. Nemo enim ipsam voluptatem quia voluptas sit aspernatur.</p>
  </div>
  <div class="footer-rule" style="top:511px"></div>
  <div class="brand footer-brand" style="left:14px;top:524px">Copper Thread</div>
  <div class="brand footer-brand" style="right:12px;top:524px">k7datagrove</div>
</section>

<section class="slide s5">
  <div class="photo" role="img" aria-label="Teal and red fibre optic light strands radiating outward"></div>
  <div class="brand brand-main" style="left:22px;top:14px;">VeraMosk</div>
  <div class="tag" style="left:196px;top:15px;width:131px;height:38px">Solutions</div>
  <div class="sol-box">
    <h3>Lorem ipsum dolor sit amet, consectet</h3>
    <p>Sed ut perspiciatis unde omnis iste natus error sit voluptatem accusantium doloremque laudantium, totam rem aperiam, eaque ipsa quae ab illo inventore veritatis et quasi architecto beatae vitae dicta sunt explicabo. Nemo enim ipsam voluptatem quia voluptas sit aspernatur aut odit aut fugit, sed quia consequuntur magni dolores eos qui ratione voluptatem sequi nesciunt. Neque porro quisquam est, qui dolore</p>
    <ul>
      <li>On the other hand, we denounce</li>
      <li>At vero eos et accusamus et iusto</li>
      <li>But I must explain to you how</li>
      <li>Sed ut perspiciatis unde omnis iste</li>
    </ul>
  </div>
  <div class="overlay">Lorem ipsum dolor sit amet, consectetur adipiscing elit, sed do eiusmod tempor</div>
  <div class="footer-rule" style="top:510px"></div>
  <div class="brand footer-brand" style="left:14px;top:524px">Copper Thread</div>
  <div class="brand footer-brand" style="right:12px;top:524px">k7datagrove</div>
</section>

<section class="slide s6">
  <div class="photo" role="img" aria-label="Dark navy digital data background with faint code"></div>
  <div class="brand brand-main">VeraMosk</div>
  <div class="thanks">Thank You</div>
</section>

</body>
</html>
```